Business Card Design Project for Heron Lending

Hello there,

We are looking for a business card design for our new Heron Lending car financing company. We are looking for a business card that will include:

- An address
- Telephone number and extension
- Employee Name
- Employee Title
- Our logo and name clearly visible

We are including our logo with this writeup, we are looking to convey friendliness, trus and memorability. Colors and everything else is up to you.

Target Market(s)

18-34 year old males and females

Industry/Entity Type

Business

```html
<!DOCTYPE html>
<html lang="en">
<head>
<meta charset="utf-8">
<title>Heron Lending – Business Card</title>
<link rel="stylesheet" href="https://fonts.googleapis.com/css2?family=Open+Sans:wght@400;600;700&display=swap">
<style>
  :root {
    --backdrop: #e6e6e6;
    --card: #f1f1ef;
    --navy: #0b3a55;
    --charcoal: #2b2a29;
    --white: #ffffff;
  }
  * { margin: 0; padding: 0; box-sizing: border-box; }
  html, body {
    width: 1200px;
    height: 675px;
    overflow: hidden;
    background: var(--backdrop);
    font-family: "Open Sans", Arial, sans-serif;
  }
  .card {
    position: absolute;
    left: 75px;
    top: 37px;
    width: 1050px;
    height: 600px;
    background: var(--card);
    overflow: hidden;
    box-shadow: 0 2px 10px rgba(0,0,0,0.12);
  }
  .card__waves {
    position: absolute;
    inset: 0;
    width: 100%;
    height: 100%;
  }
  .wave--navy { fill: var(--navy); }
  .wave--charcoal { fill: var(--charcoal); }

  .brand {
    position: absolute;
    left: 110px;
    top: 270px;
    width: 380px;
    display: flex;
    align-items: center;
    gap: 16px;
    color: var(--navy);
    font-weight: 600;
  }
  .brand__mark {
    width: 22px;
    height: 22px;
    background: var(--navy);
    flex: none;
  }
  .brand__name {
    font-size: 40px;
    line-height: 1.1;
    letter-spacing: 6px;
    text-transform: uppercase;
  }

  .person {
    position: absolute;
    right: 120px;
    top: 82px;
    text-align: right;
    color: var(--navy);
  }
  .person__name {
    font-size: 25px;
    font-weight: 700;
  }
  .person__title {
    font-size: 17px;
    font-weight: 400;
    margin-top: 2px;
  }

  .contact {
    position: absolute;
    right: 70px;
    top: 352px;
    color: var(--white);
    font-size: 20px;
    line-height: 1.45;
    text-align: right;
  }
  .contact__row {
    display: flex;
    justify-content: flex-end;
    align-items: flex-start;
    gap: 12px;
  }
  .contact__icon {
    width: 18px;
    height: 18px;
    margin-top: 5px;
    flex: none;
    fill: var(--white);
  }
</style>
</head>
<body>
  <main class="card">
    <svg class="card__waves" viewBox="0 0 1050 600" preserveAspectRatio="none" aria-hidden="true">
      <path class="wave--navy" d="M0,600 V588 C350,565 620,475 770,335 C865,245 955,205 1050,190 V600 Z"/>
      <path class="wave--charcoal" d="M0,566 C330,545 615,445 745,305 C825,222 940,188 1050,172 V178 C945,200 855,250 790,318 C650,470 360,570 0,582 Z"/>
      <path class="wave--charcoal" d="M0,542 C300,522 565,422 705,292 C785,220 900,186 1000,176 C880,202 800,244 725,308 C585,432 320,530 0,552 Z"/>
    </svg>

    <div class="brand">
      <span class="brand__mark"></span>
      <span class="brand__name">Heron<br>Lending</span>
    </div>

    <div class="person">
      <p class="person__name">Your Long Name</p>
      <p class="person__title">Your Title</p>
    </div>

    <div class="contact">
      <div class="contact__row">
        <span>00.00.00.0000</span>
        <svg class="contact__icon" viewBox="0 0 24 24" aria-hidden="true">
          <path d="M6.6 10.8a15.1 15.1 0 0 0 6.6 6.6l2.2-2.2a1 1 0 0 1 1-.25 11.4 11.4 0 0 0 3.6.57 1 1 0 0 1 1 1V20a1 1 0 0 1-1 1A17 17 0 0 1 3 4a1 1 0 0 1 1-1h3.5a1 1 0 0 1 1 1c0 1.25.2 2.45.57 3.57a1 1 0 0 1-.25 1z"/>
        </svg>
      </div>
      <div class="contact__row">
        <span>Your Commercial or<br>office address</span>
        <svg class="contact__icon" viewBox="0 0 24 24" aria-hidden="true">
          <path d="M12 2a7 7 0 0 0-7 7c0 5.25 7 13 7 13s7-7.750 7-13a7 7 0 0 0-7-7zm0 9.5A2.5 2.5 0 1 1 12 6.5a2.5 2.5 0 0 1 0 5z"/>
        </svg>
      </div>
    </div>
  </main>
</body>
</html>
```